Spy/Espionage/Counterintelligence Membership Community Needs a PowerPoint Template

We need a powerpoint template for one of our business verticals focused on spies, espionage, and counterintelligence. The name of it is "Brass Lantern Guild" and the logo is attached. Brass Lantern Guild is a community that connects people with experts in espionage and counterintelligence through an online social network, as well as in-person events. We would like to see designs that incorporate the red and black of the logo. The design should communicate mystery/suspense and peak curiosity.

Target Market(s)

Late 20s to baby boomers, male

Industry/Entity Type

Social Club

Font styles to use
Sans Serif

Colors
ec1f27
000000
ffffff

Requirements
Must have
• A user-friendly ppt template file. Incorporate basic fonts that don't have to be installed on every computer for presentations. A cover slide and a basic inside slide. A white background. I will also need graphic source files.
Nice to have
• Plenty of space for slide title and body content. Logo on every slide.
Should not have
• Inconsistency with fonts. Misalignment of images.

```html
<!DOCTYPE html>
<html lang="en">
<head>
<meta charset="utf-8">
<title>Brass Lantern Guild – Cover Slide</title>
<link rel="stylesheet" href="https://fonts.googleapis.com/css2?family=PT+Sans+Narrow:wght@400;700&family=Lato:ital,wght@0,400;1,700&display=swap">
<style>
  :root {
    --red: #ec1f27;
    --red-deep: #a8070c;
    --red-mid: #cf0f16;
    --black: #000000;
    --ink: #111111;
    --white: #ffffff;
    --mist: #eef5f9;
    --mist-deep: #dbe9f1;
  }
  html, body {
    margin: 0;
    padding: 0;
    width: 1200px;
    height: 900px;
    overflow: hidden;
    background: var(--white);
  }
  .slide {
    position: relative;
    width: 1200px;
    height: 900px;
    overflow: hidden;
    font-family: "PT Sans Narrow", "Arial Narrow", sans-serif;
  }
  .hero-band {
    position: absolute;
    left: 0; top: 0;
    width: 1200px; height: 525px;
    background: radial-gradient(ellipse at 75% 10%, var(--red-mid) 0%, var(--red-deep) 75%);
  }
  .hero-rule {
    position: absolute;
    left: 0; top: 525px;
    width: 1200px; height: 6px;
    background: var(--black);
  }
  .content-band {
    position: absolute;
    left: 0; top: 531px;
    width: 1200px; height: 280px;
    background: linear-gradient(180deg, var(--mist) 0%, var(--mist-deep) 100%);
  }
  .project-title {
    position: absolute;
    right: 72px; top: 196px;
    margin: 0;
    font-weight: 700;
    font-size: 62px;
    line-height: 1;
    color: var(--white);
  }
  .project-subtext {
    position: absolute;
    right: 72px; top: 290px;
    width: 760px;
    margin: 0;
    text-align: right;
    font-size: 26px;
    line-height: 40px;
    color: var(--white);
  }
  .brand-mark {
    position: absolute;
    left: 38px; top: 310px;
    width: 440px; height: 440px;
  }
  .brand-name {
    position: absolute;
    left: 525px; top: 628px;
    margin: 0;
    font-weight: 400;
    font-size: 88px;
    line-height: 1;
    letter-spacing: -1px;
    color: var(--ink);
  }
  .footer-bar {
    position: absolute;
    left: 0; top: 810px;
    width: 1200px; height: 90px;
    border-top: 5px solid var(--black);
    box-sizing: border-box;
    background: linear-gradient(180deg, var(--red) 0%, var(--red-deep) 100%);
  }
  .slide-number {
    position: absolute;
    left: 33px; top: 20px;
    width: 58px; height: 56px;
    border-radius: 6px;
    background: linear-gradient(180deg, #2a2a2a, var(--black));
    color: var(--white);
    font-family: "Lato", Arial, sans-serif;
    font-size: 28px;
    line-height: 56px;
    text-align: center;
  }
  .slide-date {
    position: absolute;
    left: 188px; top: 30px;
    font-family: "Lato", Arial, sans-serif;
    font-style: italic;
    font-weight: 700;
    font-size: 26px;
    color: var(--white);
  }
  .start-button {
    position: absolute;
    left: 1072px; top: 20px;
    width: 100px; height: 56px;
  }
  .start-button svg { position: absolute; left: 0; top: 0; }
  .start-label {
    position: absolute;
    left: 18px; top: 0;
    font-family: "Lato", Arial, sans-serif;
    font-size: 22px;
    line-height: 56px;
    color: var(--white);
  }
</style>
</head>
<body>
<main class="slide">
  <div class="hero-band"></div>
  <div class="hero-rule"></div>
  <div class="content-band"></div>

  <h1 class="project-title">Project Title Here</h1>
  <p class="project-subtext">Subtext here Subtext here Subtext here Subtext here Subtext here<br>Subtext here Subtext here Subtext here</p>

  <svg class="brand-mark" viewBox="0 0 440 440" aria-hidden="true">
    <circle cx="220" cy="220" r="208" fill="var(--red)" stroke="var(--black)" stroke-width="14"/>
  </svg>
  <p class="brand-name">Brass Lantern Guild</p>

  <footer class="footer-bar">
    <div class="slide-number">01</div>
    <div class="slide-date">09/06/15</div>
    <div class="start-button">
      <svg width="100" height="56" viewBox="0 0 100 56" aria-hidden="true">
        <path d="M6 0 H84 L100 28 L84 56 H6 Q0 56 0 50 V6 Q0 0 6 0 Z" fill="var(--black)"/>
      </svg>
      <span class="start-label">Start</span>
    </div>
  </footer>
</main>
</body>
</html>
```